Tally Roster survey and prize

We need an A4 poster design for a survey and competition I wish to hold. The survey will be on Poll Heron. My website www.TallyRoster.com.au will redirect the users to the survey page. I will be selecting a survey entrant at random to win a prize. The prize is $200 cash. The survey will be open for two months as the mail out of this poster will go throughout Victoria, Australia. The competition end date is yet to be decided - depends on when I can get this poster completed and the mail out done.

The mail out is targeting the Aged Care industry workers and decision makers. It hopefully will be placed on a notice board in the facilities and need to attract attention for people to visit my site and then take the survey.

The survey is for not for residents but for the workers in the facility.

Reason: Just got some feedback on required content of the poster. Text for the poster required: "The survey is for determining a market for rostering and payroll software, your assitance in taking this survey would be greatly appreciated." Martin Holloway

Target Market(s)

Workers in Aged Care industry and decision makers.

Industry/Entity Type

Industry

Requirements
Must have
• 1. Must reference the website www.TallyRoster.com.au.
2. Must mention that there is a prize of $200.
3. Must mention that entry to the competition is dependant on taking the survey.
4. Must mention the close date (date yet to be decided).
5. Must mention winning contestant will be contacted by phone.

```html
<!DOCTYPE html>
<html lang="en">
<head>
<meta charset="utf-8">
<title>Tally Roster Survey Poster</title>
<link href="https://fonts.googleapis.com/css2?family=League+Gothic&family=Roboto:wght@400;700;900&display=swap" rel="stylesheet">
<style>
  :root {
    --ink: #33343f;
    --blue: #3e63a0;
    --yellow: #fdd94a;
    --paper: #ffffff;
    --muted: #3a3a3a;
  }
  html, body {
    margin: 0;
    padding: 0;
    overflow: hidden;
    background: var(--paper);
  }
  .poster {
    position: relative;
    width: 848px;
    height: 1200px;
    overflow: hidden;
    background: var(--paper);
    font-family: "Roboto", Arial, sans-serif;
  }
  .hero-photo {
    position: absolute;
    left: 292px;
    top: 74px;
    width: 556px;
    height: 716px;
    background:
      radial-gradient(ellipse at 35% 30%, #e9d9c2 0%, rgba(233,217,194,0) 45%),
      radial-gradient(ellipse at 75% 40%, #d8d2c2 0%, rgba(216,210,194,0) 50%),
      linear-gradient(160deg, #c9c7c4 0%, #b9bcc0 45%, #8f9398 100%);
  }
  .hero-photo::before {
    content: "";
    position: absolute;
    inset: 0;
    background: linear-gradient(90deg, #ffffff 0%, rgba(255,255,255,0) 18%);
  }
  .headline {
    position: absolute;
    left: 0;
    top: 0;
    width: 848px;
    height: 820px;
  }
  .headline text {
    font-family: "League Gothic", "Oswald", sans-serif;
    stroke: var(--paper);
    stroke-width: 10px;
    stroke-linejoin: round;
    paint-order: stroke fill;
  }
  .headline .dark { fill: var(--ink); }
  .headline .accent { fill: var(--blue); }
  .headline .rule { stroke: var(--blue); stroke-width: 3px; }
  .prize-badge {
    position: absolute;
    left: 0;
    top: 0;
    width: 848px;
    height: 1200px;
    pointer-events: none;
  }
  .prize-badge .big {
    font-family: "Roboto", Arial, sans-serif;
    font-weight: 900;
    fill: var(--paper);
  }
  .prize-badge .cash {
    font-family: "Roboto", Arial, sans-serif;
    font-weight: 900;
    fill: var(--ink);
  }
  .survey-card {
    position: absolute;
    left: 28px;
    top: 838px;
    width: 350px;
    height: 264px;
    border-radius: 40px;
    background: var(--ink);
    color: var(--paper);
    text-align: center;
  }
  .survey-card__lead {
    margin: 0;
    position: absolute;
    top: 56px;
    left: 0;
    right: 0;
    font-size: 28px;
    line-height: 35px;
    font-weight: 400;
  }
  .survey-card__url {
    margin: 0;
    position: absolute;
    top: 162px;
    left: 0;
    right: 0;
    font-size: 18px;
    white-space: nowrap;
  }
  .survey-card__url strong {
    color: var(--yellow);
    font-weight: 900;
    font-size: 30px;
  }
  .closing {
    position: absolute;
    right: 50px;
    top: 1080px;
    text-align: right;
    color: #111;
  }
  .closing__date {
    margin: 0;
    font-size: 29px;
    font-weight: 400;
  }
  .closing__date span { font-weight: 700; }
  .closing__note {
    margin: 8px 0 0;
    font-size: 15px;
    color: var(--muted);
  }
  .footer-band {
    position: absolute;
    left: 0;
    bottom: 0;
    width: 848px;
    height: 34px;
    background: var(--blue);
  }
</style>
</head>
<body>
<div class="poster">

  <div class="hero-photo" role="img" aria-label="Photo of two smiling adults looking at a laptop together"></div>

  <svg class="headline" viewBox="0 0 848 820" aria-label="Take the survey, enter the competition, become the winner">
    <text class="dark" x="40" y="214" font-size="168" textLength="262" lengthAdjust="spacingAndGlyphs">TAKE THE</text>
    <text class="accent" x="40" y="349" font-size="158" textLength="262" lengthAdjust="spacingAndGlyphs">SURVEY</text>
    <text class="dark" x="40" y="459" font-size="128" textLength="262" lengthAdjust="spacingAndGlyphs">ENTER THE</text>
    <text class="accent" x="40" y="563" font-size="117" textLength="262" lengthAdjust="spacingAndGlyphs">COMPETETION</text>
    <text class="dark" x="40" y="673" font-size="134" textLength="262" lengthAdjust="spacingAndGlyphs">BECOME</text>
    <line class="rule" x1="40" y1="684" x2="302" y2="684"/>
    <text class="accent" x="40" y="777" font-size="106" textLength="262" lengthAdjust="spacingAndGlyphs">THE WINNER</text>
    <line class="rule" x1="40" y1="790" x2="302" y2="790"/>
  </svg>

  <svg class="prize-badge" viewBox="0 0 848 1200" aria-label="Win $200 cash">
    <defs>
      <clipPath id="badge-circle">
        <circle cx="603" cy="826" r="195"/>
      </clipPath>
      <filter id="drop" x="-10%" y="-10%" width="130%" height="130%">
        <feDropShadow dx="4" dy="4" stdDeviation="0" flood-color="#1f2a44" flood-opacity="0.6"/>
      </filter>
    </defs>
    <g clip-path="url(#badge-circle)">
      <rect x="400" y="620" width="420" height="420" fill="var(--blue)"/>
      <polygon points="400,972 820,884 820,1040 400,1040" fill="var(--yellow)"/>
    </g>
    <g transform="rotate(-12 603 826)" filter="url(#drop)">
      <text class="big" x="590" y="780" font-size="112" text-anchor="middle">WIN</text>
      <text class="big" x="606" y="882" font-size="120" text-anchor="middle">$200</text>
    </g>
    <text class="cash" x="662" y="985" font-size="44" text-anchor="middle" transform="rotate(-12 662 970)">CASH</text>
  </svg>

  <div class="survey-card">
    <p class="survey-card__lead">Complete our<br>online survey at</p>
    <p class="survey-card__url">www.<strong>TallyRoster</strong>.com.au</p>
  </div>

  <div class="closing">
    <p class="closing__date"><span>Closing Date</span> xx-xx-xxxx</p>
    <p class="closing__note">Winning Contestant will be Informed by Phone</p>
  </div>

  <div class="footer-band"></div>
</div>
</body>
</html>
```